Norrell Advisory WA Business Card

Create an interesting, eye catching and colourful two sided business card. We are a business consulting operation assisting SME's improve all areas of their business. We provide consulting services to assist SME's to create a culture of continuous improvement, making a positive difference in the business. Our tag line is Small changes, big rewards. We want to create a well recognised, innovative brand that can be continued throughout our website, social media and email correspondence.

Target Market(s)

Small to Medium Enterprise Business Owners

Industry/Entity Type

Business Consultant

Contact Information for Business Card

Name of Business: Norrell Advisory - Small Changes Big Rewards
Derek Holloway Ph 0407385510 Megan Holloway Ph 0407913847
Email norrelladvisorywa@mailbox-example.com
Web address TBA
FaceBook page TBA

BACKSIDE OF CARD

Providing assistance with:

• Organisation & Efficiency
• Revenue generation & Marketing
• Financial Management
• Production quality & delivery
• Systems & Process documentation
• Exit Strategy

Font styles to use
Other font styles liked:
• Calibri

Colors

Designer to choose colors to be used in the design.

Requirements
Must have
• Calibri font

```html
<!DOCTYPE html>
<html lang="en">
<head>
<meta charset="UTF-8">
<title>Norrell Advisory WA Business Card</title>
<link rel="stylesheet" href="https://fonts.googleapis.com/css2?family=Carlito:wght@400;700&family=Open+Sans:wght@400;700&family=Arimo:wght@400&display=swap">
<style>
  :root {
    --backdrop: #4a4a4c;
    --card: #ffffff;
    --brand-red: #e8392c;
    --brand-blue: #1a73bf;
    --ink: #1d1d1d;
    --dot-yellow: #f7b52a;
  }
  * { box-sizing: border-box; margin: 0; padding: 0; }
  html, body { width: 1200px; height: 1000px; overflow: hidden; }
  body {
    background: var(--backdrop);
    position: relative;
    font-family: "Carlito", "Calibri", sans-serif;
    color: var(--ink);
  }
  .card {
    position: absolute;
    background: var(--card);
    border-radius: 26px;
    overflow: hidden;
  }
  .card--front { left: 440px; top: 60px; width: 660px; height: 380px; }
  .card--back  { left: 100px; top: 510px; width: 700px; height: 400px; }

  .brand {
    display: flex; align-items: center; gap: 12px;
    color: var(--brand-red);
    font-family: "Carlito", "Calibri", sans-serif;
    font-weight: 700;
    letter-spacing: 0.5px;
  }
  .brand__dot { border-radius: 50%; background: var(--brand-red); flex: none; }

  .front__brand { position: absolute; top: 120px; left: 0; right: 0; justify-content: center; font-size: 34px; }
  .front__brand .brand__dot { width: 22px; height: 22px; }
  .front__claim {
    position: absolute; top: 200px; left: 0; right: 0; text-align: center;
    color: var(--brand-blue); font-family: "Open Sans", sans-serif; font-weight: 700; font-size: 15px;
  }
  .front__services {
    position: absolute; top: 230px; left: 30px; right: 30px; text-align: center;
    font-family: "Open Sans", sans-serif; font-size: 14px; line-height: 1.5;
  }

  .back__bar { position: absolute; left: 0; top: 40px; width: 30px; height: 105px; background: var(--brand-blue); }
  .people { position: absolute; left: 58px; top: 42px; }
  .person__name { color: var(--brand-blue); font-family: "Open Sans", sans-serif; font-weight: 700; font-size: 22px; line-height: 1.1; }
  .person__phone { font-family: "Arimo", sans-serif; font-size: 20px; margin-bottom: 10px; }

  .contacts { position: absolute; left: 50px; bottom: 70px; list-style: none; font-family: "Arimo", sans-serif; font-size: 17px; line-height: 1.4; }
  .contacts li { display: flex; align-items: center; gap: 10px; }
  .contacts svg { width: 14px; height: 14px; flex: none; }
  .contacts .icon-dot { width: 12px; height: 12px; border-radius: 50%; background: var(--brand-blue); flex: none; margin: 0 1px; }

  .back__brand { position: absolute; right: 40px; bottom: 90px; font-size: 30px; }
  .back__brand .brand__dot { width: 20px; height: 20px; }
  .back__tagline { position: absolute; right: 60px; bottom: 58px; font-family: "Open Sans", sans-serif; font-size: 15px; letter-spacing: 0.5px; }
</style>
</head>
<body>
  <section class="card card--front">
    <div class="brand front__brand"><span class="brand__dot"></span>NORRELL ADVISORY</div>
    <p class="front__claim">CREATING A CULTURE OF CONTINUOUS IMPROVEMENT</p>
    <p class="front__services">
      Organisation &amp; Efficiency | Revenue generation &amp; Marketing | Financial Management<br>
      Production quality &amp; delivery | Systems &amp; Process documentation | Exit Strategy
    </p>
  </section>

  <section class="card card--back">
    <div class="back__bar"></div>
    <div class="people">
      <p class="person__name">DEREK HOLLOWAY</p>
      <p class="person__phone">0407385510</p>
      <p class="person__name">MEGAN HOLLOWAY</p>
      <p class="person__phone">0407913847</p>
    </div>
    <ul class="contacts">
      <li>
        <svg viewBox="0 0 14 14"><rect x="1" y="3" width="12" height="9" fill="none" stroke="#1a73bf" stroke-width="1.6"/><path d="M1 3 L7 8 L13 3" fill="none" stroke="#1a73bf" stroke-width="1.6"/></svg>
        norrelladvisorywa@mailbox-example.com
      </li>
      <li>
        <svg viewBox="0 0 14 14"><circle cx="7" cy="7" r="5.8" fill="none" stroke="#1a73bf" stroke-width="1.4"/><ellipse cx="7" cy="7" rx="2.5" ry="5.8" fill="none" stroke="#1a73bf" stroke-width="1.2"/><path d="M1.2 7 H12.8" stroke="#1a73bf" stroke-width="1.2"/></svg>
        www.norrelladvisory-example.com
      </li>
      <li><span class="icon-dot"></span>norrelladvisory</li>
    </ul>
    <div class="brand back__brand"><span class="brand__dot"></span>NORRELL ADVISORY</div>
    <p class="back__tagline">SMALL CHANGES * BIG REWARDS</p>
  </section>
</body>
</html>
```